Zestora - Landing Page

Need a landing page for a journal app. The app is based on a retrospective board, where each journal entry is split into 3 sections: "What went well", "What Didn't Go Well" and "Things To Try".
The landing page should match the style of all modern web application landing pages. Think Brint, Tivalo, Mirvane. I've included screenshots of the app.
One feature that I want to highlight that is not ready yet, is an AI coach. It will offer insights based on the history of the user's journal entries
1 page

```html
<!DOCTYPE html>
<html lang="en">
<head>
<meta charset="utf-8">
<title>Zestora – Journal App Landing Page</title>
<link href="https://fonts.googleapis.com/css2?family=Montserrat:wght@300;400;600;700;800&family=Open+Sans:wght@400;600;700&display=swap" rel="stylesheet">
<style>
:root{
  --blue:#0a58c2;
  --blue-dark:#0a3f8f;
  --navy:#0b2a5c;
  --ink:#1d2230;
  --text:#5b6170;
  --light:#eef2f8;
  --panel:#e4eaf4;
  --star:#f5a623;
  --white:#ffffff;
  --line:#d8dee8;
}
*{box-sizing:border-box;margin:0;padding:0}
html,body{width:1200px;height:3476px;overflow:hidden}
body{font-family:"Open Sans",Arial,sans-serif;color:var(--text);background:var(--white);position:relative}
h1,h2,h3,.logo,.btn,.nav-links{font-family:"Montserrat",Arial,sans-serif}
.btn{display:inline-block;font-size:12px;font-weight:700;letter-spacing:.5px;padding:10px 18px;border-radius:4px;text-decoration:none;text-transform:uppercase}
.btn-fill{background:var(--blue);color:var(--white);border:2px solid var(--blue)}
.btn-line{background:var(--white);color:var(--ink);border:2px solid var(--ink)}
.btn-white{background:var(--white);color:var(--ink);border:2px solid var(--white)}

/* Navigation */
.site-nav{height:64px;display:flex;align-items:center;padding:0 100px 0 110px;box-shadow:0 2px 6px rgba(0,0,0,.06);position:relative;z-index:2;background:var(--white)}
.logo{font-size:26px;font-weight:600;color:var(--blue);letter-spacing:1px}
.nav-links{display:flex;gap:24px;margin-left:70px;list-style:none;font-size:13px;font-weight:600;color:var(--ink)}
.nav-links .active{color:var(--blue);border-bottom:2px solid var(--blue);padding-bottom:3px}
.nav-actions{margin-left:auto;display:flex;gap:16px}

/* Hero */
.hero{height:780px;position:relative;text-align:center}
.hero h1{padding-top:46px;font-size:40px;font-weight:800;color:var(--ink)}
.hero h1 span{color:var(--blue);font-weight:400}
.hero p{width:600px;margin:12px auto 0;font-size:15px;line-height:1.5}
.hero .btn{margin-top:30px}
.hero-band{position:absolute;left:0;right:0;top:282px;height:256px;background:linear-gradient(90deg,var(--navy),var(--blue))}
.app-window{position:absolute;left:136px;top:290px;width:928px;height:460px;background:var(--white);border-radius:6px;box-shadow:0 10px 30px rgba(0,0,0,.25);display:flex;overflow:hidden;text-align:left}
.app-side{width:56px;background:#1f2533;padding:18px 0;display:flex;flex-direction:column;align-items:center;gap:14px}
.app-side i{width:16px;height:16px;border-radius:50%;background:#4b5468}
.app-side i:first-child{background:#e25c5c}
.app-main{flex:1;padding:22px 28px;position:relative;background:#f7f8fb}
.app-bar{display:flex;justify-content:space-between}
.chip{font-size:11px;padding:6px 12px;border:1px solid var(--line);border-radius:4px;background:var(--white);color:var(--ink)}
.chip-save{background:#2fbf71;color:var(--white);border:none;border-radius:12px}
.entry{margin-top:20px;background:var(--white);border:1px solid var(--line);border-radius:4px;height:360px;padding:22px 28px;font-size:12px;line-height:1.75;color:var(--ink)}
.entry h4{font-family:"Montserrat",sans-serif;font-size:15px;margin-bottom:8px}
.entry b{display:block;margin-top:8px;font-size:11px;color:var(--blue)}

/* Feature rows */
.feature{position:relative}
.f1{height:460px}.f2{height:470px}.f3{height:480px}
.feature-panel{position:absolute;border-radius:0 14px 14px 0;background:linear-gradient(135deg,var(--navy),var(--blue))}
.f1 .feature-panel{left:0;top:94px;width:440px;height:250px}
.f2 .feature-panel{right:0;top:90px;width:440px;height:250px;border-radius:14px 0 0 14px}
.f3 .feature-panel{left:0;top:84px;width:430px;height:250px;background:var(--panel)}
.laptop{position:absolute;width:470px;height:300px;border-radius:10px;background:linear-gradient(180deg,#2a2f3a,#5a6272)}
.f1 .laptop{left:110px;top:116px}
.f2 .laptop{left:680px;top:110px}
.f3 .laptop{left:110px;top:104px}
.feature-copy{position:absolute;width:470px}
.f1 .feature-copy{left:644px;top:118px}
.f2 .feature-copy{left:112px;top:108px}
.f3 .feature-copy{left:644px;top:98px}
.feature-copy h2,.section-title{font-size:32px;font-weight:800;color:var(--ink);text-transform:uppercase;letter-spacing:.5px}
.feature-copy h2 span,.section-title span{color:var(--blue);font-weight:400}
.feature-copy h2::after{content:"";display:block;width:230px;height:2px;background:var(--ink);margin-top:6px}
.feature-copy p{margin-top:14px;font-size:14px;line-height:1.6}
.feature-copy .btn{margin-top:20px;background:var(--blue-dark);border-color:var(--blue-dark)}

/* Testimonials */
.clients{height:426px;background:var(--light);text-align:center;padding-top:54px;position:relative}
.quotes{display:flex;justify-content:center;gap:50px;margin-top:44px}
.quote{width:280px}
.stars{color:var(--star);font-size:20px;letter-spacing:3px}
.quote p{font-size:13px;line-height:1.6;margin-top:10px}
.quote h3{font-family:"Open Sans",sans-serif;font-weight:400;font-size:26px;color:var(--ink);margin-top:12px}
.quote + .quote{border-left:1px solid var(--line);padding-left:30px}
.arrow{position:absolute;top:210px;width:20px;height:20px}
.arrow.left{left:56px}.arrow.right{right:56px}

/* AI coach */
.ai-coach{position:absolute;top:2710px;left:0;right:0;height:300px;background:linear-gradient(90deg,var(--navy),var(--blue));text-align:center;color:var(--white);padding-top:46px}
.ai-coach h2{font-size:36px;font-weight:300;letter-spacing:1px}
.ai-coach h2 b{font-weight:800}
.ai-coach p{width:760px;margin:14px auto 0;font-size:14px;line-height:1.65;font-weight:600}
.ai-coach .btn{margin-top:24px}

/* Footer */
.site-footer{position:absolute;top:3010px;left:0;right:0;height:410px;display:flex;padding:64px 96px 0 110px;gap:0}
.foot-brand{width:340px}
.foot-brand .logo{font-size:30px}
.foot-brand p{margin-top:14px;font-size:13px;line-height:1.6}
.foot-col h3{font-size:18px;font-weight:700;color:var(--ink);text-transform:uppercase}
.foot-col h3::after{content:"";display:block;width:48px;height:2px;background:var(--blue);margin-top:4px}
.foot-links{width:210px}
.foot-links ul{list-style:none;margin-top:18px;font-size:14px;line-height:2.2}
.foot-links li:first-child{color:var(--blue)}
.foot-contact{width:300px}
.contact-item{display:flex;gap:12px;margin-top:20px;font-size:13px;line-height:1.5}
.contact-item svg{flex:none}
.contact-item strong{display:block;color:var(--ink);font-size:13px}
.socials{display:flex;gap:10px;margin-top:18px}
.socials span{width:32px;height:32px;border-radius:50%;border:2px solid var(--ink)}
.socials span:first-child{border-color:var(--blue)}
.socials span + span{background:var(--ink)}
.copyright{position:absolute;top:3420px;left:0;right:0;height:56px;background:var(--light);display:flex;align-items:center;justify-content:center;font-size:13px;color:var(--ink)}
</style>
</head>
<body>

<header class="site-nav">
  <div class="logo">ZESTORA</div>
  <ul class="nav-links">
    <li class="active">HOME</li><li>FEATURES</li><li>SOLUTIONS</li><li>ENTERPRISE</li><li>RESOURCES</li>
  </ul>
  <div class="nav-actions">
    <a class="btn btn-line">Contact Us</a>
    <a class="btn btn-fill">Log In</a>
  </div>
</header>

<section class="hero">
  <h1>MADE FOR PEOPLE. <span>BUILT FOR PRODUCTIVITY.</span></h1>
  <p>Lorem ipsum dolor sit amet, consectetur adipiscing elit, sed do eiusmod tempor incididunt ut labore et dolore magna aliqua. Quis ipsum suspendisse ultrices gravida.</p>
  <a class="btn btn-fill">Get Started</a>
  <div class="hero-band"></div>
  <div class="app-window">
    <div class="app-side"><i></i><i></i><i></i><i></i></div>
    <div class="app-main">
      <div class="app-bar"><span class="chip">+ Add Note</span><span class="chip chip-save">Save</span></div>
      <div class="entry">
        <h4>Thu Aug 22 2024</h4>
        <b>Went well</b>
        Finished the weekly planning session<br>Shipped two small fixes early<br>Kept a calm focus all morning
        <b>Didn't go well</b>
        Skipped the evening walk again<br>Too many open tabs at once
        <b>Things to try</b>
        Block one hour for deep work before lunch each day
      </div>
    </div>
  </div>
</section>

<section class="feature f1">
  <div class="feature-panel"></div>
  <div class="laptop" role="img" aria-label="Laptop showing the What Went Well journal board"></div>
  <div class="feature-copy">
    <h2>What Went <span>Well</span></h2>
    <p>Lorem ipsum dolor sit amet, consectetur adipiscing elit, sed do eiusmod tempor incididunt ut labore et dolore magna aliqua. Quis ipsum suspendisse ultrices gravida. Risus commodo viverra maecenas accumsan lacus vel facilisis. Lorem ipsum dolor sit amet, consectetur adipiscing elit, sed do eiusmod tempor incididunt ut labore et dolore magna aliqua.</p>
    <p>Lorem ipsum dolor sit amet, consectetur adipiscing elit, sed do eiusmod tempor incididunt ut labore et dolore.</p>
    <a class="btn btn-fill">Read More</a>
  </div>
</section>

<section class="feature f2">
  <div class="feature-panel"></div>
  <div class="laptop" role="img" aria-label="Laptop showing the What Didn't Go Well journal board"></div>
  <div class="feature-copy">
    <h2>What Didn't <span>Go Well</span></h2>
    <p>Lorem ipsum dolor sit amet, consectetur adipiscing elit, sed do eiusmod tempor incididunt ut labore et dolore magna aliqua. Quis ipsum suspendisse ultrices gravida. Risus commodo viverra maecenas accumsan lacus vel facilisis. Lorem ipsum dolor sit amet, consectetur adipiscing elit, sed do eiusmod tempor incididunt ut labore et dolore magna aliqua.</p>
    <p>Lorem ipsum dolor sit amet, consectetur adipiscing elit, sed do eiusmod tempor incididunt ut labore et dolore.</p>
    <a class="btn btn-fill">Read More</a>
  </div>
</section>

<section class="feature f3">
  <div class="feature-panel"></div>
  <div class="laptop" role="img" aria-label="Laptop showing the Things To Try journal board"></div>
  <div class="feature-copy">
    <h2>Things To <span>Try</span></h2>
    <p>Lorem ipsum dolor sit amet, consectetur adipiscing elit, sed do eiusmod tempor incididunt ut labore et dolore magna aliqua. Quis ipsum suspendisse ultrices gravida. Risus commodo viverra maecenas accumsan lacus vel facilisis. Lorem ipsum dolor sit amet, consectetur adipiscing elit, sed do eiusmod tempor incididunt ut labore et dolore magna aliqua.</p>
    <p>Lorem ipsum dolor sit amet, consectetur adipiscing elit, sed do eiusmod tempor incididunt ut labore et dolore.</p>
    <a class="btn btn-fill">Read More</a>
  </div>
</section>

<section class="clients">
  <h2 class="section-title">What Our <span>Clients</span></h2>
  <svg class="arrow left" viewBox="0 0 20 20"><path d="M13 3 6 10l7 7" fill="none" stroke="#0b2a5c" stroke-width="2.5"/></svg>
  <svg class="arrow right" viewBox="0 0 20 20"><path d="M7 3l7 7-7 7" fill="none" stroke="#0a58c2" stroke-width="2.5"/></svg>
  <div class="quotes">
    <div class="quote"><div class="stars">★★★★★</div><p>Lorem ipsum dolor sit amet, consectetur adipiscing elit, sed do eiusmod tempor incididunt ut labore et dolore magna aliqua.</p><h3>Dana Voss</h3></div>
    <div class="quote"><div class="stars">★★★★★</div><p>Lorem ipsum dolor sit amet, consectetur adipiscing elit, sed do eiusmod tempor incididunt ut labore et dolore magna aliqua.</p><h3>Milo</h3></div>
    <div class="quote"><div class="stars">★★★★★</div><p>Lorem ipsum dolor sit amet, consectetur adipiscing elit, sed do eiusmod tempor incididunt ut labore et dolore magna aliqua.</p><h3>Harlan</h3></div>
  </div>
</section>

<section class="ai-coach">
  <h2><b>AI</b> COACH</h2>
  <p>Lorem ipsum dolor sit amet, consectetur adipiscing elit, sed do eiusmod tempor incididunt ut labore et dolore magna aliqua. Quis ipsum suspendisse ultrices gravida. Risus commodo viverra maecenas accumsan lacus vel facilisis. Lorem ipsum dolor sit amet, consectetur adipiscing elit, sed do eiusmod tempor incididunt ut labore et dolore magna aliqua.</p>
  <a class="btn btn-white">Read More</a>
</section>

<footer class="site-footer">
  <div class="foot-brand">
    <div class="logo">ZESTORA</div>
    <p>Lorem ipsum dolor sit amet, consectetur adipiscing elit, sed do eiusmod tempor incididunt ut labore et dolore magna aliqua. Quis ipsum suspendisse ultrices gravida.</p>
  </div>
  <div class="foot-col foot-links">
    <h3>Quick Links</h3>
    <ul><li>Home</li><li>Features</li><li>Solutions</li><li>Enterprise</li><li>Resources</li></ul>
  </div>
  <div class="foot-col foot-contact">
    <h3>Contact Us</h3>
    <div class="contact-item">
      <svg width="34" height="34" viewBox="0 0 34 34"><circle cx="17" cy="17" r="17" fill="#0a58c2"/><path d="M12 10c1 0 2 2.5 2 3s-1.2 1-1 2c.6 2 2.5 4 4.5 4.6 1 .2 1.5-1 2-1s3 1 3 2-1.5 2.5-3 2.5C14 23 11 18 11 13c0-1.5.5-3 1-3z" fill="#fff"/></svg>
      <div><strong>PHONE NO</strong>(+1) (555) 014 2290</div>
    </div>
    <div class="contact-item">
      <svg width="34" height="34" viewBox="0 0 34 34"><circle cx="17" cy="17" r="17" fill="#0a58c2"/><rect x="9" y="11" width="16" height="12" rx="1.5" fill="#fff"/><path d="M9.5 12 17 18l7.5-6" fill="none" stroke="#0a58c2" stroke-width="1.5"/></svg>
      <div><strong>EMAIL:</strong>info@zestora.com</div>
    </div>
    <div class="contact-item">
      <svg width="34" height="34" viewBox="0 0 34 34"><circle cx="17" cy="17" r="17" fill="#0a58c2"/><path d="M17 8a6 6 0 0 1 6 6c0 4.5-6 11-6 11s-6-6.5-6-11a6 6 0 0 1 6-6z" fill="#fff"/><circle cx="17" cy="14" r="2.2" fill="#0a58c2"/></svg>
      <div><strong>LOCATION:</strong>Lorem Ipsum Zestora, USA</div>
    </div>
  </div>
  <div class="foot-col foot-follow">
    <h3>Follow Us</h3>
    <div class="socials"><span></span><span></span><span></span></div>
  </div>
</footer>

<div class="copyright">Copyright © 2024 · Zestora · Terms of Service and Privacy Policy</div>

</body>
</html>
```